New Business Card Design Project LORVANTI-Italy

we are LORVANTI-Italy
our company in the market for 3 years we are luxury cosmetic company and its about time for a facelift :)
i will like to have elegant luxurious and unique business card
that will give the person that get it a unique, luxurious and elegant impression
I'm VERY OPEN FOR NEW IDEAS , even duo i add a few files of things that i see on line and i like them

i add my logo as well
my website is LORVANTI.COM
(if you would like to see the main style that we have)

Target Market(s)

adult that have money :)

Industry/Entity Type

Business

Contact Information for Business Card

Name - Dario Lorvanti
Position - CEO and CO Founder
address - 4817 E Halvern
telephone - 555-384-1926
email - dario@lorvanti.com
fax - 555-384-1926
website - LORVANTI.COM

Colors
000000
959595
fbee3e
ffffff

Requirements
Must have
• big logo in GOLD color
• elegant look
• impressive
Nice to have
• not must but maybe classy pattern background
• not must but maybe emblem
• maybe clear plastic business card
Should not have
• colors
• images

```html
<!DOCTYPE html>
<html lang="en">
<head>
<meta charset="utf-8">
<title>LORVANTI-Italy Business Card</title>
<link rel="stylesheet" href="https://fonts.googleapis.com/css2?family=Oswald:wght@600&family=Open+Sans:wght@400;600;700&family=Cormorant+Garamond:wght@500&display=swap">
<style>
  :root {
    --stage: #1c1c1d;
    --card: #141415;
    --card-edge: #2a2a2b;
    --white: #ffffff;
    --silver: #959595;
    --gold: #d9aa3a;
  }
  * { margin: 0; padding: 0; box-sizing: border-box; }
  html, body { width: 1200px; height: 833px; overflow: hidden; }
  body {
    background: var(--stage);
    display: flex;
    align-items: center;
    justify-content: center;
    gap: 60px;
    font-family: "Open Sans", sans-serif;
  }
  .card {
    position: relative;
    width: 520px;
    height: 297px;
    background: var(--card);
    border: 1px solid var(--card-edge);
    border-radius: 4px;
    box-shadow: 0 20px 40px rgba(0,0,0,.5);
  }

  /* Front */
  .card--front {
    display: flex;
    align-items: center;
    justify-content: center;
    gap: 18px;
  }
  .brand-dot {
    width: 56px;
    height: 56px;
    border-radius: 50%;
    background: var(--silver);
  }
  .brand-name {
    font-family: "Cormorant Garamond", serif;
    font-weight: 500;
    font-size: 52px;
    letter-spacing: 2px;
    color: var(--silver);
  }

  /* Back */
  .identity {
    position: absolute;
    right: 262px;
    top: 112px;
    text-align: right;
  }
  .identity__name {
    font-family: "Oswald", sans-serif;
    font-weight: 600;
    font-size: 32px;
    line-height: 1;
    color: var(--white);
    text-transform: uppercase;
    letter-spacing: .3px;
  }
  .identity__role {
    margin-top: 6px;
    font-size: 14px;
    color: var(--gold);
  }
  .divider {
    position: absolute;
    left: 272px;
    top: 106px;
    width: 1.5px;
    height: 86px;
    background: var(--gold);
  }
  .contacts {
    position: absolute;
    left: 286px;
    top: 112px;
    list-style: none;
  }
  .contacts li {
    display: flex;
    align-items: center;
    gap: 7px;
    font-size: 13px;
    line-height: 18px;
    color: var(--white);
  }
  .contacts svg { width: 12px; height: 12px; fill: var(--gold); flex: none; }
  .address {
    position: absolute;
    left: 92px;
    top: 232px;
    font-size: 14px;
    color: var(--white);
  }
  .address__company { color: var(--gold); font-weight: 700; }
</style>
</head>
<body>

<section class="card card--front" aria-label="Card front">
  <span class="brand-dot" aria-hidden="true"></span>
  <span class="brand-name">LORVANTI</span>
</section>

<section class="card card--back" aria-label="Card back">
  <div class="identity">
    <h1 class="identity__name">Dario Lorvanti</h1>
    <p class="identity__role">CEO and CO Founder</p>
  </div>
  <div class="divider"></div>
  <ul class="contacts">
    <li>
      <svg viewBox="0 0 12 12" aria-label="Phone"><path d="M2.5 0.5l2 2.2-1 1.4c.6 1.6 1.8 2.8 3.4 3.4l1.4-1 2.2 2-1.3 1.8C4.7 10 1.9 7.2 0.7 1.8z"/></svg>
      555-384-1926
    </li>
    <li>
      <svg viewBox="0 0 12 12" aria-label="Fax"><rect x="3" y="0.5" width="6" height="3.5"/><rect x="0.5" y="4.5" width="11" height="5" rx="1"/><rect x="3" y="8" width="6" height="3.5" fill="#141415" stroke="#d9aa3a" stroke-width="1"/></svg>
      555-384-1926
    </li>
    <li>
      <svg viewBox="0 0 12 12" aria-label="Email"><rect x="0.5" y="2" width="11" height="8"/><path d="M0.5 2L6 6.5 11.5 2" fill="none" stroke="#141415" stroke-width="1"/></svg>
      dario@lorvanti.com
    </li>
    <li>
      <svg viewBox="0 0 12 12" aria-label="Website"><circle cx="6" cy="6" r="5.5"/><path d="M0.5 6h11M6 0.5v11M6 0.5c-2.5 3-2.5 8 0 11M6 0.5c2.5 3 2.5 8 0 11" fill="none" stroke="#141415" stroke-width=".8"/></svg>
      LORVANTI.COM
    </li>
  </ul>
  <p class="address"><span class="address__company">LORVANTI-Italy</span> - 4817 E Halvern</p>
</section>

</body>
</html>
```